Haulage company, lets use ruby red white and some 3rd color for web design. and Garvel Pryce Transport logo

Target Market(s)

Transport industry

Industry/Entity Type

transport

Number of Pages Required

2 page

Requirements
Must have
• Logo

```html
<!DOCTYPE html>
<html lang="en">
<head>
<meta charset="utf-8">
<title>Garvel Pryce Transport</title>
<link href="https://fonts.googleapis.com/css2?family=Krona+One&family=Inter:wght@400;500;600&display=swap" rel="stylesheet">
<style>
:root{
  --ruby:#9b0d16;
  --ruby-dark:#7e0a12;
  --ink:#111111;
  --text:#3a3a3a;
  --muted:#555555;
  --field:#f6f6f6;
  --white:#ffffff;
  --black:#000000;
  --map:#eeeeee;
}
*{box-sizing:border-box;margin:0;padding:0}
html,body{width:1200px;height:3930px;overflow:hidden;background:var(--white)}
body{font-family:"Inter",Arial,sans-serif;color:var(--text)}
.page{position:relative;width:1200px;height:3930px;overflow:hidden}
.abs{position:absolute}
.display{font-family:"Krona One","Arial Black",sans-serif;text-transform:uppercase;color:var(--ink)}
.btn{position:absolute;display:flex;align-items:center;justify-content:center;background:var(--ruby);color:var(--white);border-radius:30px;font-family:"Krona One","Arial Black",sans-serif;text-transform:uppercase;letter-spacing:1px}

/* hero */
.hero{left:0;top:0;width:1200px;height:668px;background:linear-gradient(180deg,#8fa9c9 0%,#c9d4df 18%,#2d5a80 24%,#36546c 38%,#5b5f63 55%,#3c3d3f 100%)}
.hero-truck{left:380px;top:150px;width:820px;height:420px;background:linear-gradient(160deg,#e8e8e6 0%,#cfd0cf 45%,#8a8a8c 100%);border-radius:6px 0 0 6px;opacity:.9}
.header{left:111px;top:38px;width:976px;height:84px;background:var(--white)}
.logo{left:24px;top:24px;font-family:"Krona One",sans-serif;font-size:17px;line-height:19px;color:var(--ink);text-transform:uppercase}
.logo small{display:block;font-size:9px;letter-spacing:6px;line-height:14px}
.nav{left:267px;top:34px;display:flex;gap:36px;font-size:13px;color:var(--ink)}
.btn-quote{left:759px;top:22px;width:197px;height:43px;font-size:13px}
.hero-welcome{left:110px;top:290px;font-size:23px;color:var(--white)}
.hero-title{left:106px;top:326px;font-size:54px;line-height:70px;color:var(--white)}
.btn-start{left:113px;top:476px;width:204px;height:53px;font-size:14px}

/* what we do */
.about{left:0;top:770px;width:1200px;height:470px;background:var(--white);box-shadow:0 8px 30px rgba(0,0,0,.08)}
.about h2{left:113px;top:58px;font-size:31px}
.about p{left:113px;top:106px;width:450px;font-size:14.5px;line-height:30px;color:var(--text)}
.btn-learn{left:111px;top:360px;width:216px;height:54px;font-size:14px}
.about-ring{left:637px;top:-16px;width:504px;height:504px;border-radius:50%;background:var(--white);box-shadow:0 6px 30px rgba(0,0,0,.12)}
.about-photo{left:660px;top:7px;width:458px;height:458px;border-radius:50%;background:radial-gradient(circle at 40% 45%,#c39a7f 0%,#7b8694 40%,#c7c9cc 70%,#e9e9e9 100%)}

/* how it works */
.section-title{left:0;width:1200px;text-align:center;font-size:31px}
.step{width:208px;height:168px;background:var(--white);box-shadow:0 6px 26px rgba(0,0,0,.08);text-align:center}
.step h3{font-family:"Krona One",sans-serif;font-size:14px;text-transform:uppercase;color:var(--ink);margin-top:52px}
.step p{font-size:11.5px;line-height:20px;color:var(--muted);padding:8px 16px 0}
.badge{width:52px;height:52px;border-radius:50%;background:var(--ruby);border:4px solid #e9e9e9;color:var(--white);text-align:center;font-family:"Krona One",sans-serif;font-size:14px;line-height:14px;padding-top:10px}
.badge span{display:block;font-family:"Inter",sans-serif;font-size:8px;font-weight:600;line-height:12px}

/* blog */
.blog{left:0;top:1798px;width:1200px;height:393px;background:var(--ruby);overflow:hidden}
.blog-title{color:var(--white)}
.post{width:407px;height:321px;overflow:visible}
.post-img{position:absolute;inset:0}
.post-a .post-img{background:linear-gradient(180deg,#3a3f3f 0%,#6a6660 45%,#1b1b1b 100%)}
.post-b .post-img{background:linear-gradient(180deg,#4d5d6a 0%,#8d7f74 45%,#1f1f22 100%)}
.post h3{position:absolute;left:22px;top:190px;font-family:"Krona One",sans-serif;font-size:19px;text-transform:uppercase;color:var(--white)}
.post p{position:absolute;left:22px;top:226px;width:370px;font-size:14.5px;line-height:26px;color:var(--white)}
.post-arrow{position:absolute;right:24px;bottom:-27px;width:54px;height:54px;border-radius:50%;background:var(--ruby);border:3px solid var(--white);display:flex;align-items:center;justify-content:center}

/* map */
.map{left:183px;top:2500px;width:793px;height:481px;background:radial-gradient(ellipse at 50% 45%,#ececec 0%,#f3f3f3 55%,#ffffff 80%)}
.tag{position:absolute;height:19px;padding:0 8px;background:var(--ruby);color:var(--white);font-size:12px;font-weight:600;line-height:19px}
.pin{position:absolute;width:12px;height:16px}

/* contact */
.field{position:absolute;background:var(--field);box-shadow:0 2px 10px rgba(0,0,0,.05);font-size:14.5px;color:#333;padding:17px 19px}
.btn-submit{left:503px;top:3407px;width:194px;height:50px;font-size:14px}

/* footer */
.footer{left:0;top:3544px;width:1200px;height:386px;background:var(--black);color:var(--white)}
.footer-nav{left:0;top:44px;width:1200px;display:flex;justify-content:center;gap:36px;font-size:13px}
.footer-row{left:111px;top:96px;width:978px;height:127px;border-top:1px solid #444;border-bottom:1px solid #444}
.footer-logo{left:64px;top:48px;font-family:"Krona One",sans-serif;font-size:21px;line-height:24px;text-transform:uppercase;color:var(--white)}
.footer-logo small{display:block;font-size:10px;letter-spacing:9px}
.divider{top:0;width:1px;height:127px;background:#444}
.icon-dot{width:40px;height:40px;border-radius:50%;background:var(--ruby);display:flex;align-items:center;justify-content:center}
.address{left:435px;top:40px;font-size:14.5px;line-height:24px}
.call{left:763px;top:48px}
.call small{font-family:"Krona One",sans-serif;font-size:9px;display:block}
.call b{font-family:"Krona One",sans-serif;font-size:15px;font-weight:400}
.social{top:261px;width:40px;height:40px;border-radius:50%;border:1px solid var(--white)}
.social.on{background:var(--ruby);border-color:var(--ruby)}
.copy{left:0;top:334px;width:1200px;text-align:center;font-size:14.5px}
.copy span{color:var(--ruby)}
</style>
</head>
<body>
<div class="page">

  <!-- hero -->
  <section class="abs hero" role="img" aria-label="Photo of two refrigerated trucks driving along a coastal road">
    <div class="abs hero-truck"></div>
  </section>
  <header class="abs header">
    <div class="abs logo">Garvel Pryce<small>Transport</small></div>
    <nav class="abs nav"><span>Home</span><span>About Us</span><span>Our Services</span><span>How It Work</span><span>Contact Us</span></nav>
    <div class="btn btn-quote">Get a Quote</div>
  </header>
  <div class="abs display hero-welcome">Welcome to</div>
  <h1 class="abs display hero-title">Garvel Pryce<br>Transport.</h1>
  <div class="btn btn-start">Get Started</div>

  <!-- what we do -->
  <section class="abs about">
    <h2 class="abs display">What We Do</h2>
    <p class="abs">Lorem ipsum dolor sit amet, consectetur adipiscing elit, sed do eiusmod tempor incididunt ut labore et dolore magna aliqua. Quis ipsum suspendisse ultrices gravida. Risus commodo viverra maecenas accumsan lacus vel facilisis. Lorem ipsum dolor sit amet, consectetur adipiscing elit, sed do eiusmod tempor incididunt ut labore et dolore magna aliqua. Quis ipsum suspendisse ultrices gravida. Risus commodo viverra maecenas accumsan lacus vel facilisis. Lorem ipsum dolor s</p>
    <div class="btn btn-learn">Learn More</div>
    <div class="abs about-ring"></div>
    <div class="abs about-photo" role="img" aria-label="Photo of a smiling truck driver leaning out of his cab window"></div>
  </section>

  <!-- how it works -->
  <h2 class="abs display section-title" style="top:1338px">How It Work</h2>
  <svg class="abs" style="left:0;top:1420px" width="1200" height="140" viewBox="0 1420 1200 140" aria-hidden="true">
    <path d="M110 1528 C170 1548 200 1540 252 1516 C300 1470 360 1430 420 1455 C450 1470 470 1490 482 1501 C540 1520 580 1470 640 1458 C680 1452 700 1456 711 1458 C760 1420 820 1438 870 1500 C900 1530 920 1545 947 1542 C1010 1520 1060 1490 1105 1462" fill="none" stroke="#9b0d16" stroke-width="1.6" stroke-dasharray="6 5"/>
    <path d="M86 1516 l6 5 -6 5 M92 1516 l6 5 -6 5" fill="none" stroke="#9b0d16" stroke-width="1.6"/>
    <path d="M1096 1462 L1116 1451 L1104 1470 L1103 1462 Z" fill="none" stroke="#9b0d16" stroke-width="1.6"/>
  </svg>
  <div class="abs step" style="left:149px;top:1522px"><h3>Lorem Ipsum</h3><p>Lorem ipsum dolor sit amet, consectetur adipiscing elit, sed do eiusmod</p></div>
  <div class="abs step" style="left:380px;top:1505px"><h3>Lorem Ipsum</h3><p>Lorem ipsum dolor sit amet, consectetur adipiscing elit, sed do eiusmod</p></div>
  <div class="abs step" style="left:608px;top:1462px"><h3>Lorem Ipsum</h3><p>Lorem ipsum dolor sit amet, consectetur adipiscing elit, sed do eiusmod</p></div>
  <div class="abs step" style="left:843px;top:1546px"><h3>Lorem Ipsum</h3><p>Lorem ipsum dolor sit amet, consectetur adipiscing elit, sed do eiusmod</p></div>
  <div class="abs badge" style="left:226px;top:1490px">01<span>Step</span></div>
  <div class="abs badge" style="left:456px;top:1475px">02<span>Step</span></div>
  <div class="abs badge" style="left:685px;top:1432px">03<span>Step</span></div>
  <div class="abs badge" style="left:921px;top:1516px">04<span>Step</span></div>

  <!-- blog -->
  <section class="abs blog">
    <svg class="abs" style="left:0;top:0" width="1200" height="393" aria-hidden="true">
      <circle cx="305" cy="75" r="55" fill="#8a0b13"/>
      <circle cx="370" cy="-40" r="150" fill="none" stroke="#850a12" stroke-width="1.5"/>
      <circle cx="1130" cy="330" r="190" fill="#8e0b14"/>
      <circle cx="1052" cy="170" r="8" fill="#8a0b13"/>
    </svg>
    <h2 class="abs display section-title blog-title" style="top:82px">Our Blog</h2>
  </section>
  <article class="abs post post-a" style="left:169px;top:1986px">
    <div class="post-img" role="img" aria-label="Photo of trucks parked at night"></div>
    <h3>Lorem Ipsum Dolor</h3>
    <p>Lorem ipsum dolor sit amet, consectetur adipiscing elit, sed do eiusmod tempor</p>
    <div class="post-arrow"><svg width="16" height="14" viewBox="0 0 16 14"><path d="M1 7h13M8 1l6 6-6 6" fill="none" stroke="#fff" stroke-width="2"/></svg></div>
  </article>
  <article class="abs post post-b" style="left:624px;top:1978px">
    <div class="post-img" role="img" aria-label="Photo of a truck driver giving a thumbs up from his cab"></div>
    <h3>Lorem Ipsum Dolor</h3>
    <p>Lorem ipsum dolor sit amet, consectetur adipiscing elit, sed do eiusmod tempor</p>
    <div class="post-arrow"><svg width="16" height="14" viewBox="0 0 16 14"><path d="M1 7h13M8 1l6 6-6 6" fill="none" stroke="#fff" stroke-width="2"/></svg></div>
  </article>

  <!-- where we go -->
  <h2 class="abs display section-title" style="top:2410px">Where We Go</h2>
  <div class="abs map" role="img" aria-label="Light grey world map"></div>
  <div class="abs" style="left:0;top:0;width:1200px;height:3000px;pointer-events:none">
    <span class="tag" style="left:216px;top:2610px">Canada</span>
    <span class="tag" style="left:361px;top:2596px">Greenland</span>
    <span class="tag" style="left:534px;top:2582px">Sweden</span>
    <span class="tag" style="left:636px;top:2593px">Lithuania</span>
    <span class="tag" style="left:500px;top:2631px">Norway</span>
    <span class="tag" style="left:546px;top:2654px">UK</span>
    <span class="tag" style="left:300px;top:2661px">Usa</span>
    <span class="tag" style="left:439px;top:2683px">Netherlands</span>
    <span class="tag" style="left:563px;top:2682px">Latvia</span>
    <span class="tag" style="left:637px;top:2679px">Turkey</span>
    <span class="tag" style="left:767px;top:2627px">China</span>
    <span class="tag" style="left:886px;top:2666px">Taiwan</span>
    <span class="tag" style="left:764px;top:2682px">Vietnam</span>
    <span class="tag" style="left:284px;top:2720px">Mexico</span>
    <span class="tag" style="left:453px;top:2720px">Spain</span>
    <span class="tag" style="left:788px;top:2724px">Bangladesh</span>
    <span class="tag" style="left:671px;top:2744px">India</span>
    <span class="tag" style="left:694px;top:2803px">Indonesia</span>
    <svg width="0" height="0" style="position:absolute"><defs><path id="pin" d="M6 16C6 16 0 9 0 6a6 6 0 0 1 12 0c0 3-6 10-6 10zM6 4a2 2 0 1 0 0.01 0z" fill="#9b0d16" fill-rule="evenodd"/></defs></svg>
    <svg class="pin" style="left:282px;top:2607px"><use href="#pin"/></svg>
    <svg class="pin" style="left:441px;top:2607px"><use href="#pin"/></svg>
    <svg class="pin" style="left:567px;top:2596px"><use href="#pin"/></svg>
    <svg class="pin" style="left:606px;top:2596px"><use href="#pin"/></svg>
    <svg class="pin" style="left:561px;top:2619px"><use href="#pin"/></svg>
    <svg class="pin" style="left:534px;top:2656px"><use href="#pin"/></svg>
    <svg class="pin" style="left:282px;top:2657px"><use href="#pin"/></svg>
    <svg class="pin" style="left:537px;top:2680px"><use href="#pin"/></svg>
    <svg class="pin" style="left:578px;top:2657px"><use href="#pin"/></svg>
    <svg class="pin" style="left:628px;top:2695px"><use href="#pin"/></svg>
    <svg class="pin" style="left:761px;top:2642px"><use href="#pin"/></svg>
    <svg class="pin" style="left:862px;top:2662px"><use href="#pin"/></svg>
    <svg class="pin" style="left:753px;top:2698px"><use href="#pin"/></svg>
    <svg class="pin" style="left:267px;top:2712px"><use href="#pin"/></svg>
    <svg class="pin" style="left:522px;top:2698px"><use href="#pin"/></svg>
    <svg class="pin" style="left:759px;top:2735px"><use href="#pin"/></svg>
    <svg class="pin" style="left:727px;top:2760px"><use href="#pin"/></svg>
    <svg class="pin" style="left:792px;top:2794px"><use href="#pin"/></svg>
  </div>

  <!-- get in touch -->
  <h2 class="abs display section-title" style="top:3062px">Get In Touch</h2>
  <div class="field" style="left:213px;top:3144px;width:385px;height:51px">First Name</div>
  <div class="field" style="left:615px;top:3144px;width:385px;height:51px">Last Name</div>
  <div class="field" style="left:213px;top:3211px;width:385px;height:51px">Email</div>
  <div class="field" style="left:615px;top:3211px;width:385px;height:51px">Phone</div>
  <div class="field" style="left:213px;top:3279px;width:789px;height:103px">How Can We Help?</div>
  <div class="btn btn-submit">Submit</div>

  <!-- footer -->
  <footer class="abs footer">
    <nav class="abs footer-nav"><span>Home</span><span>About Us</span><span>Our Services</span><span>How It Work</span><span>Contact Us</span></nav>
    <div class="abs footer-row">
      <div class="abs footer-logo">Garvel Pryce<small>Transport</small></div>
      <div class="abs divider" style="left:357px"></div>
      <div class="abs divider" style="left:680px"></div>
      <div class="abs icon-dot" style="left:378px;top:44px"><svg width="12" height="16" viewBox="0 0 12 16"><path d="M6 16C6 16 0 9 0 6a6 6 0 0 1 12 0c0 3-6 10-6 10zM6 4a2 2 0 1 0 0.01 0z" fill="#fff" fill-rule="evenodd"/></svg></div>
      <div class="abs address">12b Garvel Pryce Transport Lorem<br>ipsum dolor sit consectetur</div>
      <div class="abs icon-dot" style="left:710px;top:40px"><svg width="16" height="16" viewBox="0 0 24 24"><path d="M6.6 10.8a15 15 0 0 0 6.6 6.6l2.2-2.2a1 1 0 0 1 1-.25 11.4 11.4 0 0 0 3.6.57 1 1 0 0 1 1 1V20a1 1 0 0 1-1 1A17 17 0 0 1 3 4a1 1 0 0 1 1-1h3.5a1 1 0 0 1 1 1c0 1.25.2 2.45.57 3.57a1 1 0 0 1-.25 1z" fill="#fff"/></svg></div>
      <div class="abs call"><small>Call Us</small><b>+1 555 010 2030</b></div>
    </div>
    <div class="abs social on" style="left:505px" aria-label="Social link"></div>
    <div class="abs social" style="left:556px" aria-label="Social link"></div>
    <div class="abs social" style="left:607px" aria-label="Social link"></div>
    <div class="abs social" style="left:656px" aria-label="Social link"></div>
    <p class="abs copy">©Copyrights 2024 &nbsp;<span>Garvel Pryce Transport</span> &nbsp;| &nbsp;All Rights Reserved</p>
  </footer>
</div>
</body>
</html>
```